QVR business card

Need a business card for a company that provides instructional design and elearning development services. The website is here: http://quorvane.studio/

I'm attaching a current logo, as well as the old business card design. While I like to keep it clean, the old design is too simplistic for my liking. The only idea I want to reuse from the old design is placing industry jargon on the back of the card, just need a better way to present it. But if you have other ideas for the back--feel free to experiment.

Please use the colors complementary to the color we have on the website. Thank you!

```html
<!DOCTYPE html>
<html lang="en">
<head>
<meta charset="utf-8">
<title>QVR Business Card</title>
<link rel="stylesheet" href="https://fonts.googleapis.com/css2?family=Arimo:wght@400;700&family=Montserrat:wght@600;700&display=swap">
<style>
  :root {
    --backdrop: #e4e4e4;
    --card-white: #ffffff;
    --card-dark: #1d1d1d;
    --card-dark-soft: #2a2a2a;
    --teal: #1fb3a0;
    --gold: #d3c38c;
    --ink: #2b2b2b;
    --icon: #3a3a3a;
    --divider: #333333;
  }
  * { margin: 0; padding: 0; box-sizing: border-box; }
  html, body { width: 1200px; height: 800px; overflow: hidden; }
  body {
    background: var(--backdrop);
    font-family: "Arimo", Arial, sans-serif;
    position: relative;
  }
  .card {
    position: absolute;
    top: 250px;
    width: 525px;
    height: 300px;
    border-radius: 22px;
    overflow: hidden;
  }
  /* Back of card */
  .card-back {
    left: 50px;
    background: var(--card-dark);
  }
  .card-back__texture {
    position: absolute;
    inset: 0;
    background: radial-gradient(ellipse at 50% 50%, var(--card-dark-soft), var(--card-dark) 75%);
  }
  .card-back__content {
    position: relative;
    height: 100%;
    display: flex;
    flex-direction: column;
    justify-content: center;
    align-items: center;
    text-align: center;
    gap: 2px;
  }
  .jargon {
    color: var(--gold);
    font-weight: 700;
    font-size: 20px;
    line-height: 1.2;
    letter-spacing: 0.3px;
    text-transform: uppercase;
  }
  .tagline {
    color: #ffffff;
    font-weight: 700;
    font-size: 47px;
    line-height: 1.15;
    margin: 8px 0 10px;
    letter-spacing: 1px;
  }
  /* Front of card */
  .card-front {
    left: 625px;
    background: var(--card-white);
  }
  .brand {
    position: absolute;
    left: 48px;
    top: 0;
    height: 100%;
    display: flex;
    align-items: center;
    gap: 12px;
  }
  .brand__dot {
    width: 34px;
    height: 34px;
    border-radius: 50%;
    background: var(--teal);
  }
  .brand__name {
    font-family: "Montserrat", Arial, sans-serif;
    font-weight: 700;
    font-size: 50px;
    color: var(--gold);
    letter-spacing: 2px;
  }
  .divider {
    position: absolute;
    left: 262px;
    top: 82px;
    width: 1.5px;
    height: 136px;
    background: var(--divider);
  }
  .contact {
    position: absolute;
    left: 290px;
    top: 96px;
  }
  .contact__name {
    font-family: "Montserrat", Arial, sans-serif;
    font-weight: 700;
    font-size: 21px;
    color: var(--teal);
    margin-bottom: 16px;
  }
  .contact__list { list-style: none; }
  .contact__item {
    display: flex;
    align-items: center;
    gap: 8px;
    font-size: 13px;
    color: var(--ink);
    margin-bottom: 9px;
  }
  .contact__icon { width: 15px; height: 15px; flex: none; }
</style>
</head>
<body>

<section class="card card-back" aria-label="Back of business card">
  <div class="card-back__texture" role="img" aria-label="Faint repeating graduation cap pattern on a dark background"></div>
  <div class="card-back__content">
    <p class="jargon">Mobile Learning SCORM Instructional<br>Design LMS MOOCs eLearning HTML5</p>
    <h2 class="tagline">HOW CAN WE HELP?</h2>
    <p class="jargon">Adult Learning Theory Gamification<br>Classroom xAPI Blended Learning</p>
  </div>
</section>

<section class="card card-front" aria-label="Front of business card">
  <div class="brand">
    <span class="brand__dot"></span>
    <span class="brand__name">QVR</span>
  </div>
  <div class="divider"></div>
  <div class="contact">
    <h1 class="contact__name">Marek Havlin</h1>
    <ul class="contact__list">
      <li class="contact__item">
        <svg class="contact__icon" viewBox="0 0 16 16" aria-hidden="true">
          <circle cx="8" cy="8" r="8" fill="var(--icon)"/>
          <path d="M5.2 4.2c.4-.3.9-.2 1.1.2l.6 1.2c.2.4 0 .8-.3 1l-.4.3c.4.9 1.1 1.7 2 2.1l.3-.4c.2-.3.7-.5 1-.3l1.2.6c.4.2.5.7.2 1.1l-.5.6c-.5.5-1.3.6-2 .3-1.8-.8-3.2-2.2-4-4-.3-.7-.2-1.5.3-2z" fill="#fff"/>
        </svg>
        555-013-2740
      </li>
      <li class="contact__item">
        <svg class="contact__icon" viewBox="0 0 16 16" aria-hidden="true">
          <circle cx="8" cy="8" r="8" fill="var(--icon)"/>
          <rect x="4" y="5.2" width="8" height="5.6" rx="0.6" fill="#fff"/>
          <path d="M4.3 5.6 8 8.4l3.7-2.8" stroke="var(--icon)" stroke-width="0.8" fill="none"/>
        </svg>
        mhavlin@quorvane.studio
      </li>
      <li class="contact__item">
        <svg class="contact__icon" viewBox="0 0 16 16" aria-hidden="true">
          <circle cx="8" cy="8" r="8" fill="var(--icon)"/>
          <g stroke="#fff" stroke-width="0.8" fill="none">
            <circle cx="8" cy="8" r="4"/>
            <ellipse cx="8" cy="8" rx="1.7" ry="4"/>
            <path d="M4 8h8M4.6 6h6.8M4.6 10h6.8"/>
          </g>
        </svg>
        www.quorvane.studio
      </li>
    </ul>
  </div>
</section>

</body>
</html>
```